For Sale Sign for Real Estate Agency

We need a For Sale Sign designed for our agency. I want a very simple/elegant sign that says "For Sale" towards the top of the sign (not in huge letters). Most of the sign should be a design/picture with our name and phone number somewhere at the bottom.

One significant detail, it's important that our logo not be too big or the center piece of the sign. Since our company name has the word "rent" in it, people assume the house is for rent, instead of for sale.

I attached our logo and a rough outline of the format I'm looking for.

Again, I'm looking for elegant and simple! Thanks for your time

Industry/Entity Type

Real Estate

Colors

Designer to choose colors to be used in the design.

Requirements
Must have
Nice to have
Should not have
• Nothing tacky!
• Our logo/company name should not be too big or the center piece of the sign. Since our company name has the word "rent" in it, people assume the house is for rent, instead of for sale.

```html
<!DOCTYPE html>
<html lang="en">
<head>
<meta charset="utf-8">
<title>For Sale Sign</title>
<link href="https://fonts.googleapis.com/css2?family=Montserrat:wght@500;600;700&display=swap" rel="stylesheet">
<style>
  :root {
    --backdrop: #e8ebef;
    --sign-white: #ffffff;
    --navy: #1f1f4f;
    --accent-red: #e3262c;
    --house-roof: #2f6560;
    --house-wall: #cfc8bb;
    --house-shadow: #e4e4e4;
  }
  * { margin: 0; padding: 0; box-sizing: border-box; }
  html, body {
    width: 1200px;
    height: 960px;
    overflow: hidden;
    background: var(--backdrop);
    font-family: "Montserrat", sans-serif;
  }
  .canvas {
    position: relative;
    width: 1200px;
    height: 960px;
  }
  .sign {
    position: absolute;
    left: 284px;
    top: 50px;
    width: 632px;
    height: 860px;
    background: var(--sign-white);
    box-shadow: 0 10px 30px rgba(20, 25, 45, 0.18);
    overflow: hidden;
  }
  .sign-heading {
    position: absolute;
    top: 70px;
    left: 0;
    right: 0;
    text-align: center;
    color: var(--navy);
    font-weight: 600;
    font-size: 76px;
    letter-spacing: 3px;
    line-height: 1;
  }
  .house-artwork {
    position: absolute;
    left: 74px;
    top: 168px;
    width: 484px;
    height: 322px;
    border-radius: 6px;
    background:
      linear-gradient(180deg, var(--house-roof) 0%, var(--house-roof) 30%, var(--house-wall) 55%, var(--house-wall) 85%, var(--house-shadow) 100%);
    opacity: 0.9;
  }
  .contact-band {
    position: absolute;
    left: 0;
    right: 0;
    top: 540px;
    bottom: 0;
    background: var(--navy);
    border-top: 10px solid var(--accent-red);
  }
  .agency-name {
    position: absolute;
    right: 90px;
    top: 580px;
    text-align: right;
    color: var(--sign-white);
    font-weight: 500;
    line-height: 1;
  }
  .agency-name__primary {
    display: block;
    font-size: 80px;
    letter-spacing: -1px;
  }
  .agency-name__secondary {
    display: block;
    margin-top: 12px;
    font-size: 36px;
    letter-spacing: 9px;
    margin-right: -9px;
  }
  .agency-phone {
    position: absolute;
    left: 0;
    right: 0;
    top: 774px;
    display: flex;
    justify-content: center;
    align-items: center;
    gap: 16px;
    color: var(--sign-white);
    font-weight: 600;
    font-size: 50px;
    letter-spacing: 2px;
    line-height: 1;
  }
  .agency-phone__icon {
    width: 42px;
    height: 42px;
    flex: none;
  }
</style>
</head>
<body>
<main class="canvas">
  <section class="sign">
    <h1 class="sign-heading">FOR SALE</h1>

    <div class="house-artwork" role="img" aria-label="Illustration of a two-storey house with green roof and beige walls"></div>

    <div class="contact-band" aria-hidden="true"></div>

    <p class="agency-name">
      <span class="agency-name__primary">Harborline</span>
      <span class="agency-name__secondary">Realty</span>
    </p>

    <p class="agency-phone">
      <svg class="agency-phone__icon" viewBox="0 0 42 42" aria-hidden="true">
        <circle cx="21" cy="21" r="18" fill="none" stroke="var(--sign-white)" stroke-width="3"/>
        <path fill="none" stroke="var(--sign-white)" stroke-width="3" stroke-linecap="round" stroke-linejoin="round"
              d="M15,12 L18,12 L20,17 L17.5,19 C18.5,22 20,23.5 23,24.5 L25,22 L30,24 L30,27 C30,29 28,30 26,30 C19,29 13,23 12,16 C12,14 13,12 15,12 Z"/>
      </svg>
      <span>401-555-0148</span>
    </p>
  </section>
</main>
</body>
</html>
```